Brookmere Osteopathy flyer

I want a clean clear DL flyer (but also want an A4 poster) promoting a new Osteopathic business in a semi rural area in Tasmania (Australia).
It can have pictures like the examples attached to show people what Osteopathy is (its like Chiropractic and physiotherapy).
I am the sole practioner and am male, so any pictures would be best to be a white male if possible.
I've attached some wording, you can use all, or none of it
I don't have a phone number for the business yet
info@brookmereosteopathy.example
www.brookmereosteopathy.example
Target Market(s)
Australians, from tradies, professionals, babies to retired people
Industry/Entity Type
Health
Look and feel

```html
<!DOCTYPE html>
<html lang="en">
<head>
<meta charset="utf-8">
<title>Brookmere Osteopathy – Poster</title>
<link href="https://fonts.googleapis.com/css2?family=Montserrat:wght@700;800;900&family=Oswald:wght@500&family=Roboto+Condensed:wght@400&display=swap" rel="stylesheet">
<style>
  :root{
    --blue:#1596d4;
    --blue-deep:#0f8fcf;
    --orange:#f48d32;
    --ink:#2f2f33;
    --paper:#ffffff;
    --stage:#e9edf0;
    --line:#cfd3d6;
  }
  *{margin:0;padding:0;box-sizing:border-box}
  html,body{width:1200px;height:1200px;overflow:hidden;background:var(--stage)}
  .poster{
    position:absolute;left:190px;top:20px;width:1109px;height:1570px;
    background:var(--paper);transform:scale(0.739);transform-origin:0 0;
    overflow:hidden;font-family:"Montserrat",sans-serif;
    box-shadow:0 6px 30px rgba(0,0,0,.12);
  }
  .abs{position:absolute}
  .brand{left:113px;top:208px;width:380px;text-align:center;color:var(--blue);
    font-weight:800;font-size:44px;line-height:52px;letter-spacing:1px;text-transform:uppercase}
  .headline{left:596px;top:66px;font-weight:800;font-size:104px;line-height:82px;letter-spacing:-1px}
  .headline span{display:block}
  .c-blue{color:var(--blue)} .c-orange{color:var(--orange)}
  .subhead{left:590px;top:404px;font-weight:800;font-size:38px;line-height:41px;color:var(--ink);z-index:3}
  .photo-main{left:0;top:455px;width:660px;height:500px;
    background:linear-gradient(135deg,#f2f2f2 0%,#e8d4c4 38%,#3fb0e3 62%,#2a9fd6 100%);
    clip-path:polygon(0 0,50% 0,62% 4%,80% 16%,100% 28%,100% 100%,0 100%)}
  .spine{left:60px;top:850px}
  .photo-circle{border-radius:50%;border:10px solid #fff;outline:1.5px solid var(--blue)}
  .pc-1{left:693px;top:550px;width:350px;height:350px;background:linear-gradient(160deg,#ece9e6,#c9a58b 60%,#e9e7e4)}
  .pc-2{left:531px;top:730px;width:250px;height:250px;background:linear-gradient(180deg,#efefef,#d8c0ac 55%,#f4f4f4)}
  .pc-3{left:738px;top:775px;width:310px;height:310px;background:linear-gradient(170deg,#d9d9d9,#e6c3aa 55%,#f1f1f1)}
  .panel{left:700px;top:965px;width:338px;height:548px;background:var(--blue-deep);
    border-radius:0 0 30px 30px;z-index:0}
  .pc-1,.pc-2,.pc-3{z-index:1}
  .banner{left:680px;top:1098px;width:375px;height:104px;background:var(--orange);
    border-radius:12px 0 0 12px;color:#fff;font-family:"Oswald",sans-serif;font-weight:500;
    font-size:41px;line-height:43px;text-align:center;padding-top:9px;z-index:2}
  .banner span{display:inline-block;transform:scaleX(.86)}
  .benefits{left:720px;top:1208px;width:298px;z-index:2}
  .benefit{color:#fff;font-weight:800;font-size:19px;line-height:21px;text-align:center;
    height:73px;display:flex;align-items:center;justify-content:center;border-bottom:1.5px solid rgba(255,255,255,.55)}
  .benefit:last-child{border-bottom:none}
  .reasons-title{left:70px;top:1006px;font-weight:800;font-size:35px;line-height:36px;color:var(--blue)}
  .reasons{top:1093px;font-family:"Roboto Condensed",sans-serif;font-size:19px;color:var(--ink);list-style:none}
  .reasons li{height:31px;display:flex;align-items:center;gap:7px}
  .reasons li svg{flex:none}
  .reasons-a{left:74px} .reasons-b{left:352px}
  .divider{left:70px;top:1255px;width:587px;height:2px;background:var(--line)}
  .cta{left:72px;top:1272px;font-family:"Oswald",sans-serif;font-weight:500;font-size:33px;line-height:34px;
    transform:scaleX(.8);transform-origin:0 0}
  .phone{left:284px;top:1268px;font-family:"Oswald",sans-serif;font-weight:500;font-size:78px;line-height:90px;
    color:var(--orange);transform:scaleX(.78);transform-origin:0 0;white-space:nowrap}
  .email{left:290px;top:1354px;font-weight:700;font-size:18px;color:var(--ink);display:flex;align-items:center;gap:10px}
  .address{left:95px;top:1398px;width:535px;height:48px;background:var(--blue);
    clip-path:polygon(3% 0,97% 0,100% 100%,0 100%);border-radius:12px 12px 0 0;
    color:#fff;font-weight:800;font-size:25px;text-align:center;line-height:46px}
  .website{left:67px;top:1442px;width:593px;height:71px;background:var(--orange);
    border:3px solid var(--blue);border-radius:36px;color:#fff;font-weight:800;font-size:26px;
    text-align:center;line-height:64px}
</style>
</head>
<body>
<main class="poster">
  <div class="abs brand">Brookmere<br>Osteopathy</div>

  <h1 class="abs headline">
    <span class="c-blue">FEEL</span>
    <span class="c-orange">BETTER</span>
    <span class="c-blue">MOVE</span>
    <span class="c-orange">FREELY</span>
  </h1>

  <div class="abs photo-main" role="img" aria-label="Photo of an osteopath treating a man's neck and shoulder"></div>
  <p class="abs subhead">OSTEOPATHY<br>HELPS EASE PAIN &amp;<br>RESTORE MOBILITY.</p>
  <svg class="abs spine" width="600" height="150" viewBox="0 0 600 150" role="img" aria-label="Illustration of a spine">
    <path d="M5 125 C120 40 330 10 595 120 L590 140 C330 45 140 70 20 130 Z" fill="var(--orange)"/>
  </svg>

  <div class="abs panel"></div>
  <div class="abs photo-circle pc-1" role="img" aria-label="Photo of a practitioner stretching a man's neck"></div>
  <div class="abs photo-circle pc-2" role="img" aria-label="Photo of a woman receiving neck treatment lying down"></div>
  <div class="abs photo-circle pc-3" role="img" aria-label="Photo of a woman receiving head and jaw treatment"></div>

  <div class="abs banner"><span>OSTEOPATHS USE A<br>COMBINATION OF</span></div>
  <div class="abs benefits">
    <div class="benefit">RELIEVE PAIN,<br>RESTORE MOVEMENT.</div>
    <div class="benefit">MOVE BETTER,<br>FEEL BETTER.</div>
    <div class="benefit">PAIN RELIEF.<br>NATURAL MOVEMENT.</div>
    <div class="benefit">OSTEOPATHY<br>FOR PAIN &amp; MOBILITY.</div>
  </div>

  <h2 class="abs reasons-title">COMMON REASONS<br>PEOPLE VISIT <span class="c-orange">AN OSTEOPATH:</span></h2>
  <ul class="abs reasons reasons-a">
    <li><svg width="14" height="14" viewBox="0 0 14 14"><circle cx="7" cy="7" r="6" fill="none" stroke="var(--orange)" stroke-width="1.4"/><path d="M4 7.2l2 2 4-4" fill="none" stroke="var(--orange)" stroke-width="1.4"/></svg>Back / neck pain</li>
    <li><svg width="14" height="14" viewBox="0 0 14 14"><circle cx="7" cy="7" r="6" fill="none" stroke="var(--orange)" stroke-width="1.4"/><path d="M4 7.2l2 2 4-4" fill="none" stroke="var(--orange)" stroke-width="1.4"/></svg>Headaches / migraines</li>
    <li><svg width="14" height="14" viewBox="0 0 14 14"><circle cx="7" cy="7" r="6" fill="none" stroke="var(--orange)" stroke-width="1.4"/><path d="M4 7.2l2 2 4-4" fill="none" stroke="var(--orange)" stroke-width="1.4"/></svg>Joint and muscle pain</li>
    <li><svg width="14" height="14" viewBox="0 0 14 14"><circle cx="7" cy="7" r="6" fill="none" stroke="var(--orange)" stroke-width="1.4"/><path d="M4 7.2l2 2 4-4" fill="none" stroke="var(--orange)" stroke-width="1.4"/></svg>Pregnancy-related discomfort</li>
    <li><svg width="14" height="14" viewBox="0 0 14 14"><circle cx="7" cy="7" r="6" fill="none" stroke="var(--orange)" stroke-width="1.4"/><path d="M4 7.2l2 2 4-4" fill="none" stroke="var(--orange)" stroke-width="1.4"/></svg>Disc related issues</li>
  </ul>
  <ul class="abs reasons reasons-b">
    <li><svg width="14" height="14" viewBox="0 0 14 14"><circle cx="7" cy="7" r="6" fill="none" stroke="var(--orange)" stroke-width="1.4"/><path d="M4 7.2l2 2 4-4" fill="none" stroke="var(--orange)" stroke-width="1.4"/></svg>Sciatica</li>
    <li><svg width="14" height="14" viewBox="0 0 14 14"><circle cx="7" cy="7" r="6" fill="none" stroke="var(--orange)" stroke-width="1.4"/><path d="M4 7.2l2 2 4-4" fill="none" stroke="var(--orange)" stroke-width="1.4"/></svg>Plantar fasciitis</li>
    <li><svg width="14" height="14" viewBox="0 0 14 14"><circle cx="7" cy="7" r="6" fill="none" stroke="var(--orange)" stroke-width="1.4"/><path d="M4 7.2l2 2 4-4" fill="none" stroke="var(--orange)" stroke-width="1.4"/></svg>Tendonitis / Bursitis</li>
    <li><svg width="14" height="14" viewBox="0 0 14 14"><circle cx="7" cy="7" r="6" fill="none" stroke="var(--orange)" stroke-width="1.4"/><path d="M4 7.2l2 2 4-4" fill="none" stroke="var(--orange)" stroke-width="1.4"/></svg>Adhesive capsulitis (frozen shoulder)</li>
    <li><svg width="14" height="14" viewBox="0 0 14 14"><circle cx="7" cy="7" r="6" fill="none" stroke="var(--orange)" stroke-width="1.4"/><path d="M4 7.2l2 2 4-4" fill="none" stroke="var(--orange)" stroke-width="1.4"/></svg>Tennis / Golfers elbow</li>
  </ul>

  <div class="abs divider"></div>
  <p class="abs cta"><span class="c-blue">CONTACT TODAY<br>TO BOOK YOUR</span><br><span class="c-orange">APPOINTMENT</span></p>
  <p class="abs phone">04XX XXX XXX</p>
  <p class="abs email">
    <svg width="16" height="12" viewBox="0 0 16 12"><rect x="0.5" y="0.5" width="15" height="11" fill="var(--blue)"/><path d="M1 1l7 6 7-6" fill="none" stroke="#fff" stroke-width="1.3"/></svg>
    info@brookmereosteopathy.example
  </p>
  <div class="abs address">48 Willow Creek road, Brookmere</div>
  <div class="abs website">www.brookmereosteopathy.example</div>
</main>
</body>
</html>
```